Design for a real estate wev portal

Contents and features of the site
---------------------------------
Website in 5 languages: French, Dutch, English, German, Spanish.
English name of the site: Harbor Nest Place
Main purpose of the site:
- allow people to rent their house/ appartment for flatsharing purposes.
- help people wanting to find a room in flatsharing
- help people to find additional roommates for their flatsharing
Key interaction sequence:
1. I create a "group" of people who have common interest/hobbies
2. People who have the same interests/hobbies join my group
3. I look for a house/appartment to host my group
Website structure will be the following:
- Home
- Groups
-- Look for a group
--- Join a group
-- Create a group
- Properties
-- Look for a house/appartement
-- Apply
- Sales conditions
- Contact
- My account
-- My profile
-- My groups OR my properties
Your mission
------------
The client has no graphical guidelines, simply a logo (see attached).
We need a (responsive compliant) design for the following pages (we expect PSD's from you. No HTML nor CSS):
1. homepage (see example and wireframe attached)
2. properties search result list (see wireframe attached)
3. "detailed" form for properties
4. groups search result list
5. "detailed" form for groups
6. my account page
FOR THE COMPETITION step we only expect from you the design of first 2 screens.
Based on that, we will select the designer who will win the project, and will have to design the 4 remaining screens.
Target Market(s)
B2C
Industry/Entity Type
Real Estate
Number of Pages Required
5+ page
Look and feel
Each slider illustrates characteristics of the customer's brand and the style your logo design should communicate.

```html
<!DOCTYPE html>
<html lang="en">
<head>
<meta charset="utf-8">
<title>Harbor Nest Place</title>
<link rel="stylesheet" href="https://fonts.googleapis.com/css2?family=Montserrat:wght@400;500;600;700&family=Open+Sans:wght@400;600;700&display=swap">
<style>
:root{
  --green:#66bb44;
  --green-text:#5db53b;
  --green-dark:#4f9f32;
  --dark:#333333;
  --ink:#1f1f1f;
  --body:#555555;
  --muted:#777777;
  --panel:#f1f1f1;
  --line:#d6d6d6;
  --footer:#5f5f5f;
  --white:#ffffff;
}
*{box-sizing:border-box;margin:0;padding:0}
html,body{width:1200px;height:2961px;overflow:hidden}
body{position:relative;background:var(--white);font-family:"Open Sans",Arial,sans-serif;color:var(--body)}
.abs{position:absolute}
.heading{font-family:"Montserrat",Arial,sans-serif;font-weight:700;text-transform:uppercase;color:var(--green-text)}

/* header */
.site-header{position:absolute;left:0;top:0;width:1200px;height:148px;background:var(--white);z-index:2}
.lang-btn{left:99px;top:32px;width:150px;height:35px;border:2px solid var(--dark);display:flex;align-items:center;gap:10px;padding-left:8px;font:600 13px "Montserrat",sans-serif;color:var(--ink)}
.lang-flag{width:34px;height:22px;background:#2b3f8c;border-radius:2px}
.caret{width:0;height:0;border-left:5px solid transparent;border-right:5px solid transparent;border-top:6px solid var(--ink)}
.login-btn{left:839px;top:32px;width:99px;height:35px;background:var(--green);color:var(--white);display:flex;align-items:center;justify-content:center;gap:7px;font:600 13px "Montserrat",sans-serif}
.account-btn{left:951px;top:32px;width:150px;height:35px;border:2px solid var(--dark);color:var(--ink);display:flex;align-items:center;justify-content:center;gap:7px;font:600 13px "Montserrat",sans-serif}
.main-nav a{position:absolute;top:104px;font:600 15px "Montserrat",sans-serif;color:var(--ink);text-decoration:none;text-transform:uppercase}
.logo-disc{left:492px;top:40px;width:216px;height:178px;border-radius:0 0 108px 108px;background:var(--white);z-index:3;display:flex;flex-direction:column;align-items:center;padding-top:44px}
.logo-disc .dot{width:26px;height:26px;border-radius:50%;background:var(--green);margin-bottom:6px}
.brand-name{font:600 22px/1.1 "Montserrat",sans-serif;color:var(--dark);text-align:center;width:190px}

/* hero */
.hero{left:0;top:148px;width:1200px;height:513px;background:linear-gradient(180deg,#1f3a3f 0%,#31494a 40%,#4a4a3a 70%,#2a3540 100%)}
.hero-title{left:310px;top:257px;width:582px;height:69px;background:var(--green);color:var(--white);font:700 38px/69px "Montserrat",sans-serif;text-align:center;text-transform:uppercase}
.hero-text{left:190px;top:374px;width:820px;color:var(--white);font:600 14.5px/1.9 "Open Sans",sans-serif;text-align:center}
.hero-btn{left:533px;top:470px;width:134px;height:47px;border:2px solid var(--white);color:var(--white);font:500 15px/43px "Montserrat",sans-serif;text-align:center;text-transform:uppercase}
.slider-dot{left:1141px;width:16px;height:16px;border-radius:50%;background:#d8d8d8}
.slider-dot.active{background:var(--green);border:2px solid var(--white)}

/* accommodation cards */
.section-title{font-size:21px;text-align:center;width:520px}
.card{width:233px;height:205px;border:3px solid #dcdcdc;background:var(--white)}
.card .photo{height:157px}
.card .label{height:42px;background:var(--green);color:var(--white);font:600 13.5px/42px "Open Sans",sans-serif;text-align:center}
.divider{left:99px;top:1025px;width:1002px;height:1px;background:var(--line)}

/* spotlight */
.spot-photo{width:160px;height:152px}
.spot-box{width:300px;height:136px;background:var(--panel);border:1px solid #cfcfcf;padding:16px 16px 0 16px}
.spot-box h3{font:500 16px "Montserrat",sans-serif;color:var(--ink);margin-bottom:8px}
.spot-box p{font:400 12px/1.75 "Open Sans",sans-serif;color:var(--muted)}
.more-btn{height:40px;background:var(--green);color:var(--white);font:600 14px/40px "Open Sans",sans-serif;text-align:center}

/* selling points */
.points-band{left:0;top:1599px;width:1200px;height:381px;background:linear-gradient(180deg,#6cc046 0%,#62b83f 60%,#57ab37 100%)}
.point-box{top:1676px;width:493px;height:229px;border:2px solid var(--white);text-align:center;color:var(--white);padding-top:28px}
.point-box h3{font:500 23px/1.55 "Montserrat",sans-serif;margin-bottom:18px}
.point-box p{font:400 12px/2 "Open Sans",sans-serif;padding:0 34px;opacity:.92}

/* faq */
.faq-item{left:172px;width:856px;height:85px;background:linear-gradient(180deg,#f7f7f7,#e6e6e6);border:1px solid #cfcfcf;padding:17px 24px 0 24px;font:400 12.5px/1.9 "Open Sans",sans-serif;color:var(--dark)}
.faq-item a{color:var(--green-text);font-weight:600;text-decoration:none}
.cta{top:2519px;width:341px;height:49px;color:var(--white);font:500 17px/49px "Montserrat",sans-serif;text-align:center;text-transform:uppercase}

/* footer */
.site-footer{left:0;top:2629px;width:1200px;height:332px;background:var(--footer)}
.footer-brand{left:450px;top:2690px;width:300px;display:flex;flex-direction:column;align-items:center}
.footer-brand .dot{width:26px;height:26px;border-radius:50%;background:var(--white);margin-bottom:8px}
.footer-brand span{font:600 28px "Montserrat",sans-serif;color:var(--white)}
.footer-nav span{position:absolute;top:2830px;font:600 15px "Montserrat",sans-serif;color:var(--white);text-transform:uppercase}
.footer-rule{left:99px;top:2886px;width:1002px;height:1px;background:#9a9a9a}
.copyright{left:99px;top:2913px;font:600 13.5px "Open Sans",sans-serif;color:var(--white)}
.social{top:2906px;width:34px;height:34px;border-radius:50%;border:2px solid var(--white)}
</style>
</head>
<body>

<header class="site-header">
  <div class="abs lang-btn"><span class="lang-flag"></span>ENGLISH<span class="caret"></span></div>
  <div class="abs login-btn">
    <svg width="13" height="13" viewBox="0 0 13 13"><path d="M1 6.5h7M5.5 3.5l3 3-3 3" stroke="#fff" stroke-width="2" fill="none"/><path d="M8 1h4v11H8" stroke="#fff" stroke-width="1.6" fill="none"/></svg>LOGIN</div>
  <div class="abs account-btn">
    <svg width="12" height="13" viewBox="0 0 12 13"><circle cx="6" cy="3.5" r="3" fill="#1f1f1f"/><path d="M0 13c0-4 2.5-6 6-6s6 2 6 6z" fill="#1f1f1f"/></svg>MY ACCOUNT</div>
  <nav class="main-nav">
    <a style="left:99px">Home</a>
    <a style="left:187px">About Us</a>
    <a style="left:312px">Our Services</a>
    <a style="left:760px">Accommodation</a>
    <a style="left:993px">Contact Us</a>
  </nav>
</header>
<div class="abs logo-disc"><span class="dot"></span><div class="brand-name">Harbor Nest Place</div></div>

<section class="abs hero" role="img" aria-label="Modern house with a lit pool terrace at dusk"></section>
<h1 class="abs hero-title">Harbor Nest Place</h1>
<p class="abs hero-text">Sed ut perspiciatis unde omnis iste natus error sit voluptatem accusantium doloremque laudantium, totam rem aperiam, eaque ipsa quae ab illo inventore veritatis et quasi architecto.</p>
<div class="abs hero-btn">Read More</div>
<span class="abs slider-dot active" style="top:353px"></span>
<span class="abs slider-dot" style="top:377px"></span>
<span class="abs slider-dot" style="top:399px"></span>
<span class="abs slider-dot" style="top:421px"></span>
<span class="abs slider-dot" style="top:444px"></span>

<h2 class="abs heading section-title" style="left:81px;top:714px">Searching for accommodation</h2>
<h2 class="abs heading section-title" style="left:601px;top:714px">I have a house for rent</h2>

<div class="abs card" style="left:97px;top:768px"><div class="photo" role="img" aria-label="Suburban house with a green lawn" style="background:linear-gradient(180deg,#9fb7c9,#6f8a5a 60%,#4e8a2e)"></div><div class="label">I want to rent a room right now!</div></div>
<div class="abs card" style="left:351px;top:768px"><div class="photo" role="img" aria-label="Modern glass and dark house among trees" style="background:linear-gradient(180deg,#8fb6d8,#4c5a55 55%,#5e7f3a)"></div><div class="label">I want to join a group</div></div>
<div class="abs card" style="left:616px;top:768px"><div class="photo" role="img" aria-label="Street of new family houses" style="background:linear-gradient(180deg,#a9cbe8,#c9b9a0 55%,#6f9c45)"></div><div class="label">I want to advertise!</div></div>
<div class="abs card" style="left:871px;top:768px"><div class="photo" role="img" aria-label="Brick house with a front garden" style="background:linear-gradient(180deg,#6fa7e0,#9a5a45 55%,#5f9038)"></div><div class="label">Why is flat sharing interesting?</div></div>

<div class="abs divider"></div>

<h2 class="abs heading section-title" style="left:81px;top:1073px">Under the spotlight</h2>
<h2 class="abs heading section-title" style="left:601px;top:1073px">Under the spotlight</h2>

<div class="abs spot-photo" style="left:99px;top:1135px" role="img" aria-label="Lit modern villa reflected in a pool" aria-hidden="false"><div style="width:100%;height:100%;background:linear-gradient(180deg,#1d3c8a,#c08a3a 55%,#1e3f7a)"></div></div>
<div class="abs spot-box" style="left:259px;top:1143px"><h3>A Nice Group</h3><p>Sed ut perspiciatis unde omnis iste natus error sit voluptatem accusantium Sed ut perspiciatis unde omnis iste natus.</p></div>
<div class="abs spot-photo" style="left:99px;top:1323px" role="img" aria-label="White house behind leafy trees"><div style="width:100%;height:100%;background:linear-gradient(180deg,#cfe0c8,#8c9f86 50%,#4f7f32)"></div></div>
<div class="abs spot-box" style="left:259px;top:1331px"><h3>Another Nice Group</h3><p>Sed ut perspiciatis unde omnis iste natus error sit voluptatem accusantium Sed ut perspiciatis unde omnis iste natus.</p></div>
<div class="abs more-btn" style="left:409px;top:1504px;width:150px">See More Groups</div>

<div class="abs spot-photo" style="left:642px;top:1135px" role="img" aria-label="Blue-grey house with a garage"><div style="width:100%;height:100%;background:linear-gradient(180deg,#a8c4de,#7a8a9c 50%,#6f8f4a)"></div></div>
<div class="abs spot-box" style="left:801px;top:1143px"><h3>House</h3><p>Sed ut perspiciatis unde omnis iste natus error sit voluptatem accusantium Sed ut perspiciatis unde omnis iste natus.</p></div>
<div class="abs spot-photo" style="left:642px;top:1323px" role="img" aria-label="Cottage style house on a lawn"><div style="width:100%;height:100%;background:linear-gradient(180deg,#b9d4ee,#8a6a5a 50%,#5e9a36)"></div></div>
<div class="abs spot-box" style="left:801px;top:1331px"><h3>Apartment</h3><p>Sed ut perspiciatis unde omnis iste natus error sit voluptatem accusantium Sed ut perspiciatis unde omnis iste natus.</p></div>
<div class="abs more-btn" style="left:948px;top:1504px;width:152px">See More Houses</div>

<section class="abs points-band" role="img" aria-label="City skyline tinted green"></section>
<div class="abs point-box" style="left:99px"><h3>Key Selling Points For<br>The Roommates</h3><p>Sed ut perspiciatis unde omnis iste natus error sit voluptatem accusantium doloremque laudantium, totam rem aperiam, eaque ipsa quae ab illo inven tore veritatis et quasi archi tecto beatae vitae dicta sunt explicabo.</p></div>
<div class="abs point-box" style="left:608px"><h3>Key Selling Points For<br>The Owners</h3><p>Sed ut perspiciatis unde omnis iste natus error sit voluptatem accusantium doloremque laudantium, totam rem aperiam, eaque ipsa quae ab illo inven tore veritatis et quasi archi tecto beatae vitae dicta sunt explicabo.</p></div>

<h2 class="abs heading" style="left:200px;top:2032px;width:800px;text-align:center;font-size:21px">Everything you need to know about flatsharing</h2>
<div class="abs faq-item" style="top:2094px">Sed ut perspiciatis unde omnis iste natus error sit voluptatem accusantium doloremque laudantium, totam rem aperiam, eaque ipsa quae ab illo inventore veritatis et quasi architecto beatae vitae dicta sunt explicabo. <a>Read More</a></div>
<div class="abs faq-item" style="top:2197px">Sed ut perspiciatis unde omnis iste natus error sit voluptatem accusantium doloremque laudantium, totam rem aperiam, eaque ipsa quae ab illo inventore veritatis et quasi architecto beatae vitae dicta sunt explicabo. <a>Read More</a></div>
<div class="abs faq-item" style="top:2300px">Sed ut perspiciatis unde omnis iste natus error sit voluptatem accusantium doloremque laudantium, totam rem aperiam, eaque ipsa quae ab illo inventore veritatis et quasi architecto beatae vitae dicta sunt explicabo. <a>Read More</a></div>
<div class="abs more-btn" style="left:525px;top:2418px;width:150px">All Questions &gt;&gt;</div>

<div class="abs cta" style="left:245px;background:var(--green)">Pre - Defined Searches</div>
<div class="abs cta" style="left:614px;background:var(--dark)">Tools and Informations</div>

<footer class="abs site-footer"></footer>
<div class="abs footer-brand"><span class="dot"></span><span>Harbor Nest Place</span></div>
<nav class="footer-nav">
  <span style="left:196px">Home</span>
  <span style="left:289px">|</span>
  <span style="left:342px">About Us</span>
  <span style="left:469px">|</span>
  <span style="left:522px">Accommodation</span>
  <span style="left:680px">|</span>
  <span style="left:763px">Blog</span>
  <span style="left:848px">|</span>
  <span style="left:901px">Contact Us</span>
</nav>
<div class="abs footer-rule"></div>
<p class="abs copyright">© 2016 Harbor Nest Place. All Rights Reserved</p>
<span class="abs social" style="left:911px"></span>
<span class="abs social" style="left:950px"></span>
<span class="abs social" style="left:989px"></span>
<span class="abs social" style="left:1028px"></span>
<span class="abs social" style="left:1067px"></span>

</body>
</html>
```